Local fast-growing company in the service sector

We are looking for a modern business card design, which should also appear on our letterheads

Target Market(s)

Private and industrial sectors

Contact Information for Business Card

Vorname Name
Kellberger Str. 18
73614 Schorndorf
Tel.: 07146-839214-0
Name@agentur-kvtl.de

Colors
9d9d9d
919191
aaaaaa

Requirements
Must have
• The logo (file) in silver

```html
<!DOCTYPE html>
<html lang="de">
<head>
<meta charset="utf-8">
<title>KVTL – Visitenkarte</title>
<link rel="stylesheet" href="https://fonts.googleapis.com/css2?family=Montserrat:wght@400;600&display=swap">
<style>
  :root {
    --page-bg: #ececec;
    --card-light: #d4d4d4;
    --card-mid: #aaaaaa;
    --panel-dark: #3a3a3c;
    --panel-deep: #2a2a2c;
    --text-light: #f2f2f2;
    --text-soft: #dcdcdc;
    --brand-silver: #919191;
    --card-edge: rgba(255, 255, 255, 0.7);
  }
  * { margin: 0; padding: 0; box-sizing: border-box; }
  html, body {
    width: 1200px;
    height: 969px;
    overflow: hidden;
    background: var(--page-bg);
    font-family: "Montserrat", Arial, sans-serif;
  }
  .canvas {
    position: relative;
    width: 1200px;
    height: 969px;
  }
  .business-card {
    position: absolute;
    left: 188px;
    top: 248px;
    width: 873px;
    height: 495px;
    border-radius: 26px;
    border: 2px solid var(--card-edge);
    overflow: hidden;
    background: linear-gradient(135deg, var(--card-light) 0%, #c4c4c4 55%, var(--card-mid) 100%);
    box-shadow: 0 18px 40px rgba(0, 0, 0, 0.18);
  }
  .contact-panel {
    position: absolute;
    left: 52px;
    top: 0;
    width: 530px;
    height: 100%;
    background: linear-gradient(160deg, #5a5a5c 0%, var(--panel-dark) 45%, var(--panel-deep) 100%);
    opacity: 0.88;
  }
  .contact-block {
    position: absolute;
    left: 107px;
    top: 170px;
    color: var(--text-light);
  }
  .person-name {
    font-size: 32px;
    font-weight: 600;
    line-height: 40px;
    letter-spacing: 0.3px;
    margin-bottom: 10px;
  }
  .address-line {
    font-size: 19px;
    font-weight: 400;
    color: var(--text-soft);
    line-height: 27px;
  }
  .contact-list {
    list-style: none;
    margin-top: 12px;
  }
  .contact-item {
    display: flex;
    align-items: center;
    gap: 14px;
    font-size: 19px;
    color: var(--text-soft);
    line-height: 28px;
  }
  .contact-icon {
    width: 17px;
    height: 17px;
    fill: var(--text-soft);
    flex-shrink: 0;
  }
  .brand-lockup {
    position: absolute;
    left: 519px;
    top: 215px;
    display: flex;
    align-items: center;
    gap: 14px;
  }
  .brand-square {
    width: 56px;
    height: 56px;
    background: var(--brand-silver);
  }
  .brand-name {
    font-size: 52px;
    font-weight: 600;
    line-height: 60px;
    color: var(--brand-silver);
    letter-spacing: 1px;
  }
</style>
</head>
<body>
  <main class="canvas">
    <section class="business-card">
      <div class="contact-panel"></div>

      <div class="contact-block">
        <h1 class="person-name">Vorname Name</h1>
        <p class="address-line">Kellberger Str. 18</p>
        <p class="address-line">73614 Schorndorf</p>
        <ul class="contact-list">
          <li class="contact-item">
            <svg class="contact-icon" viewBox="0 0 24 24" aria-hidden="true"><path d="M6.6 10.8a15.1 15.1 0 0 0 6.6 6.6l2.2-2.2c.3-.3.7-.4 1-.2 1.1.4 2.3.6 3.6.6.6 0 1 .4 1 1V20c0 .6-.4 1-1 1A17 17 0 0 1 3 4c0-.6.4-1 1-1h3.5c.6 0 1 .4 1 1 0 1.3.2 2.5.6 3.6.1.3 0 .7-.2 1z"/></svg>
            <span>07146-839214-0</span>
          </li>
          <li class="contact-item">
            <svg class="contact-icon" viewBox="0 0 24 24" aria-hidden="true"><path d="M2 5h20v14H2z M3.5 6.5 12 13l8.5-6.5" fill="none" stroke="#dcdcdc" stroke-width="2"/><path d="M3 6h18l-9 7z"/></svg>
            <span>Name@agentur-kvtl.de</span>
          </li>
          <li class="contact-item">
            <svg class="contact-icon" viewBox="0 0 24 24" aria-hidden="true"><circle cx="12" cy="12" r="9" fill="none" stroke="#dcdcdc" stroke-width="2"/><path d="M3 12h18M12 3c3 3 3 15 0 18M12 3c-3 3-3 15 0 18" fill="none" stroke="#dcdcdc" stroke-width="1.6"/></svg>
            <span>www.agentur-kvtl.de</span>
          </li>
        </ul>
      </div>

      <div class="brand-lockup">
        <span class="brand-square"></span>
        <span class="brand-name">KVTL</span>
      </div>
    </section>
  </main>
</body>
</html>
```